Health and Fitness Club requires a stunning and simple website

We are a health and fitness club based in Dubai, when we launch we will be the biggest club in the country, we will also have the 2 largest activity rooms in the country, we are setting a new standard in the industry by offering one thing, our attitude.

Our attitude means the following:
unlike other clubs we have no hidden charges or fees
our members can join daily, monthly, 6 months or annually
our service and facility are comparable to 5* hotel gyms
our equipment is second to none
our space is the biggest in the country
we do not force our members to use our in-house personal trainers - you can bring your own and we will not charge them entry!
we will have a cutting edge brawnmesh box in our gym with classes by the best trainers in the country
we will be providing free-lance personal trainers a platform to engage customers, grow their business and even use our activity rooms for classes

Basically we will be a gym like no other, simply because we are gym people and we hate the restrictive practices and hidden charges by other gyms, so we are making our own gym which focuses on quality and service.

All of this has to be communicated in the style of the website, the colors of the website we want to be limited to the logo colors as this will be the same theme running throughout the gym.

The landing page of the website HAS to incorporate elements from our social media presences, this basically is the usual, chirplo, snapvault, kinwall. We can have these as a sidebar, the centre of the page should display the latest article from our blog (also on the website) Also we need to have a calendar for activities and classes on the front page. The menu should have links to the following:
Latest News
About us
Team
Gallery
Membership
Classes
Member Log In
Contact Us
Location

The style of the website has to be similar to the logo, particularly in terms of the fonts used.

```html
<!DOCTYPE html>
<html lang="en">
<head>
<meta charset="utf-8">
<title>Ironhold Fitness</title>
<link href="https://fonts.googleapis.com/css2?family=Bebas+Neue&family=Open+Sans:wght@300;400;600;700&display=swap" rel="stylesheet">
<style>
  :root {
    --red: #c3121c;
    --red-dark: #9e0e16;
    --maroon: #2a0508;
    --ink: #222;
    --text: #555;
    --muted: #888;
    --paper: #f3f3f3;
    --line: #dcdcdc;
    --white: #fff;
  }
  * { margin: 0; padding: 0; box-sizing: border-box; }
  html, body { width: 942px; height: 1200px; overflow: hidden; }
  body {
    position: relative;
    background: var(--paper);
    font-family: "Open Sans", Arial, sans-serif;
    color: var(--text);
  }
  .display { font-family: "Bebas Neue", Impact, sans-serif; font-weight: 400; }

  /* Header */
  .brand {
    position: absolute; left: 104px; top: 30px;
    display: flex; align-items: center; gap: 10px;
    color: var(--ink); font-weight: 700; font-size: 18px; letter-spacing: .5px;
  }
  .brand-mark { width: 34px; height: 34px; border-radius: 50%; background: var(--red); }
  .social {
    position: absolute; right: 102px; top: 50px;
    display: flex; gap: 14px; font-size: 12px; font-weight: 700; color: var(--ink);
  }
  .search {
    position: absolute; left: 672px; top: 84px; width: 164px; height: 16px;
    background: #e4e4e4; border: none;
    font: 400 9px "Open Sans", Arial, sans-serif; color: #777; padding: 2px 6px;
  }

  /* Navigation */
  .main-nav {
    position: absolute; left: 102px; top: 108px; width: 738px; height: 50px;
    background: var(--red); display: flex; justify-content: space-between; align-items: center;
    padding: 0 16px;
  }
  .main-nav a { color: var(--white); text-decoration: none; font-size: 19px; letter-spacing: .2px; }

  /* Hero */
  .hero {
    position: absolute; left: 102px; top: 168px; width: 738px; height: 291px;
    background: var(--maroon); overflow: hidden;
  }
  .hero-photo {
    position: absolute; left: 300px; top: 0; width: 438px; height: 291px;
    background: linear-gradient(90deg, var(--maroon) 0%, #6a1116 45%, #8a2a1e 70%, #4a0c0e 100%);
  }
  .hero-title {
    position: absolute; left: 40px; top: 94px; color: var(--white); line-height: .95;
  }
  .hero-title .big { font-size: 46px; display: block; }
  .hero-title .small { font-size: 33px; display: block; }
  .hero-arrows { position: absolute; left: 40px; top: 230px; }

  /* Welcome */
  .welcome-title {
    position: absolute; left: 102px; top: 484px; width: 738px; text-align: center;
    color: var(--red); font-size: 24px;
  }
  .welcome-text {
    position: absolute; left: 102px; top: 530px; width: 740px;
    font-size: 10.8px; line-height: 18.8px; font-weight: 300; letter-spacing: -.05px;
  }

  .section-title { position: absolute; color: var(--red); font-size: 24px; }

  /* Articles */
  .article { position: absolute; top: 674px; width: 236px; font-size: 10.8px; line-height: 18.8px; font-weight: 300; }
  .article time { display: block; font-size: 14px; font-weight: 300; color: #444; margin-bottom: 9px; }
  .article h3 { color: var(--red); font-size: 10.8px; font-weight: 700; line-height: 18.8px; }

  /* Gallery */
  .gallery-item { position: absolute; width: 158px; }
  .gallery-photo { height: 95px; }
  .gallery-item p { font-size: 8.5px; color: var(--ink); margin-top: 5px; margin-left: -2px; }

  /* Calendar */
  .calendar { position: absolute; left: 605px; top: 863px; width: 235px; }
  .cal-head {
    height: 36px; background: linear-gradient(#555, #333);
    display: flex; justify-content: space-between; align-items: center; padding: 0 12px;
    color: var(--white);
  }
  .cal-head .month { font-size: 22px; }
  .cal-days { display: grid; grid-template-columns: repeat(7, 1fr); font-size: 7.5px; font-weight: 600; color: #444; text-align: center; padding: 10px 0 4px; }
  .cal-grid { display: grid; grid-template-columns: repeat(7, 1fr); border-top: 1px solid var(--line); border-left: 1px solid var(--line); }
  .cal-grid span {
    position: relative; height: 33.5px; display: flex; align-items: center; justify-content: center;
    font-size: 9.5px; font-weight: 600; color: var(--ink); background: #f7f7f7;
    border-right: 1px solid var(--line); border-bottom: 1px solid var(--line);
  }
  .cal-grid .out { color: #aaa; font-weight: 400; }
  .cal-grid .event::after {
    content: ""; position: absolute; bottom: 6px; left: 50%; width: 2px; height: 2px;
    margin-left: -1px; border-radius: 50%; background: #333;
  }
  .cal-grid .today { background: var(--red); color: var(--white); }
  .cal-grid .today::after { background: var(--white); }

  /* Footer */
  .site-footer {
    position: absolute; left: 0; top: 1122px; width: 942px; height: 78px; background: var(--red);
    color: var(--white); text-align: center;
  }
  .footer-nav { padding-top: 20px; font-size: 11px; }
  .footer-nav a { color: var(--white); text-decoration: none; }
  .footer-nav .sep { margin: 0 11px; }
  .copyright { font-size: 11px; margin-top: 8px; }
</style>
</head>
<body>

<header>
  <div class="brand"><span class="brand-mark"></span>Ironhold Fitness</div>
  <div class="social"><span>kinwall</span><span>chirplo</span><span>snapvault</span></div>
  <input class="search" type="text" placeholder="Search" aria-label="Search">
</header>

<nav class="main-nav display">
  <a href="#">Latest News</a>
  <a href="#">About Us</a>
  <a href="#">Team</a>
  <a href="#">Gallery</a>
  <a href="#">Membership</a>
  <a href="#">Classes</a>
  <a href="#">Member Log In</a>
  <a href="#">Contact Us</a>
  <a href="#">Location</a>
</nav>

<section class="hero">
  <div class="hero-photo" role="img" aria-label="Photo of a woman and a man lifting dumbbells against a red backdrop"></div>
  <h1 class="hero-title display">
    <span class="big">Our Space is the</span>
    <span class="small">Biggest in the Country</span>
  </h1>
  <svg class="hero-arrows" width="40" height="22" viewBox="0 0 40 22" aria-label="Slide controls">
    <polyline points="13,2 4,11 13,20" fill="none" stroke="#c3121c" stroke-width="3"/>
    <polyline points="27,2 36,11 27,20" fill="none" stroke="#c3121c" stroke-width="3"/>
  </svg>
</section>

<h2 class="welcome-title display">Welcome to Ironhold Fitness</h2>
<p class="welcome-text">Lorem Ipsum is simply dummy text of the printing and typesetting industry. Lorem Ipsum has been the industry's standard dummy text ever since the 1500s, when an unknown printer took a galley of type and scrambled it to make a type specimen book. It has survived not only five centuries, but also the leap into electronic typesetting, remaining essentially unchanged. It was popularised in the 1960s with the release of Typeworks sheets containing Lorem Ipsum passages, and more recently with desktop publishing software like Pagecraft Studio including versions of Lorem Ipsum.</p>

<h2 class="section-title display" style="left:102px; top:638px;">Latest Article</h2>
<article class="article" style="left:102px;">
  <time>12-2-2014</time>
  <h3>Lorem Ipsum is simply dummy text of the printing and typesetting industry.</h3>
  <p>Lorem Ipsum has been the industry's standard dummy text ever since the 1500s, when an unknown printer took</p>
</article>
<article class="article" style="left:354px;">
  <time>12-2-2014</time>
  <h3>Lorem Ipsum is simply dummy text of the printing and typesetting industry.</h3>
  <p>Lorem Ipsum has been the industry's standard dummy text ever since the 1500s, when an unknown printer took</p>
</article>
<article class="article" style="left:606px;">
  <time>12-2-2014</time>
  <h3>Lorem Ipsum is simply dummy text of the printing and typesetting industry.</h3>
  <p style="color:var(--muted)">Lorem Ipsum has been the industry's standard dummy text ever since the 1500s, when an unknown printer took</p>
</article>

<h2 class="section-title display" style="left:102px; top:822px;">Gallery</h2>
<figure class="gallery-item" style="left:102px; top:863px;">
  <div class="gallery-photo" role="img" aria-label="Photo of a man curling a dumbbell" style="background:linear-gradient(90deg,#c98a64,#e9e4e0);"></div>
  <p>Neque porro quisquam est qui</p>
</figure>
<figure class="gallery-item" style="left:265px; top:863px;">
  <div class="gallery-photo" role="img" aria-label="Photo of two women training with weights" style="background:linear-gradient(90deg,#8a2a24,#c9a07f,#6a7a5a);"></div>
  <p>Neque porro quisquam est qui</p>
</figure>
<figure class="gallery-item" style="left:429px; top:863px;">
  <div class="gallery-photo" role="img" aria-label="Photo of a man lifting a dumbbell sideways in a dark room" style="background:linear-gradient(90deg,#2a2c33,#4d4e55,#23242a);"></div>
  <p>Neque porro quisquam est qui</p>
</figure>
<figure class="gallery-item" style="left:102px; top:981px;">
  <div class="gallery-photo" role="img" aria-label="Photo of a man training on a cable machine in a gym" style="background:linear-gradient(90deg,#5a5a5a,#b58a6a,#6b6b6b);"></div>
  <p>Neque porro quisquam est qui</p>
</figure>
<figure class="gallery-item" style="left:265px; top:981px;">
  <div class="gallery-photo" role="img" aria-label="Photo of a trainer guiding a woman with a dumbbell" style="background:linear-gradient(90deg,#9a9a9a,#c8a48a,#eeeeee);"></div>
  <p>Neque porro quisquam est qui</p>
</figure>
<figure class="gallery-item" style="left:429px; top:981px;">
  <div class="gallery-photo" role="img" aria-label="Black and white photo of a fit couple posing" style="background:linear-gradient(90deg,#141414,#5c5c5c,#1c1c1c);"></div>
  <p>Neque porro quisquam est qui</p>
</figure>

<h2 class="section-title display" style="left:602px; top:822px;">Calendar Activity</h2>
<section class="calendar" aria-label="Activity calendar">
  <div class="cal-head">
    <svg width="8" height="12" viewBox="0 0 8 12"><polyline points="6,1 1,6 6,11" fill="none" stroke="#888" stroke-width="2"/></svg>
    <span class="month display">January 2014</span>
    <svg width="8" height="12" viewBox="0 0 8 12"><polyline points="2,1 7,6 2,11" fill="none" stroke="#fff" stroke-width="2"/></svg>
  </div>
  <div class="cal-days"><span>MON</span><span>TUE</span><span>WED</span><span>THU</span><span>FRI</span><span>SAT</span><span>SUN</span></div>
  <div class="cal-grid">
    <span class="out event">30</span><span>1</span><span class="event">2</span><span>3</span><span>4</span><span>5</span><span>6</span>
    <span>7</span><span>8</span><span>9</span><span>10</span><span>11</span><span class="today event">12</span><span>13</span>
    <span>14</span><span>15</span><span class="event">16</span><span class="event">17</span><span>18</span><span>19</span><span>20</span>
    <span class="event">21</span><span>22</span><span>23</span><span>24</span><span>25</span><span>26</span><span>27</span>
    <span>28</span><span>29</span><span>30</span><span>31</span><span class="out">1</span><span class="out">2</span><span class="out">3</span>
  </div>
</section>

<footer class="site-footer">
  <nav class="footer-nav">
    <a href="#">Latest News</a><span class="sep">|</span><a href="#">About us</a><span class="sep">|</span><a href="#">Team</a><span class="sep">|</span><a href="#">Gallery</a><span class="sep">|</span><a href="#">Membership</a><span class="sep">|</span><a href="#">Classes</a><span class="sep">|</span><a href="#">Member Log In</a><span class="sep">|</span><a href="#">Contact Us</a><span class="sep">|</span><a href="#">Location</a>
  </nav>
  <p class="copyright">© Copyrights Compnay Name, All Rights Reserved</p>
</footer>

</body>
</html>
```